Harbor Crestline (Business Card Design)

Need business cards designed. Something modern, chic, and sleek. Mabye the back of the card should be the navy blue that is in the logo and then just the logo on the back.

Target Market(s)

Those in the hotel, office, and renovation industry

Contact Information for Business Card

1. Logo 2. Dorian Fenwick 3. CEO/Founder 4. Phone: (833) HarbCre / (833) 427-2731 5. Email: dorian@theharborcrestline.com 6. Website: www.theharborcrestline.com

Font styles to use
Other font styles liked:
• Look at the logo font and base the font for everything else off of that.

Colors
0054AA
0677BA
7BADD7
CADEEF
E8F1F8

Requirements
Must have
• Colors that are associated in the logo
Nice to have
• Sleek modern clean and chic design.

```html
<!DOCTYPE html>
<html lang="en">
<head>
<meta charset="utf-8">
<title>Harbor Crestline – Business Card</title>
<link href="https://fonts.googleapis.com/css2?family=Montserrat:wght@500;700;800&family=Open+Sans:wght@400;600&display=swap" rel="stylesheet">
<style>
  :root{
    --navy:#0f1a4a;
    --navy-deep:#0b1440;
    --navy-soft:#1b2a6b;
    --gold:#d3a84a;
    --white:#ffffff;
    --ink:#141a33;
    --stage:#2a2b30;
  }
  *{box-sizing:border-box;margin:0;padding:0}
  html,body{width:1200px;height:780px;overflow:hidden}
  body{
    background:var(--stage);
    display:flex;align-items:center;justify-content:center;gap:40px;
    font-family:"Open Sans",sans-serif;
  }
  .card{
    position:relative;width:560px;height:320px;overflow:hidden;
    box-shadow:0 18px 40px rgba(0,0,0,.45);
  }
  .card::after{
    content:"";position:absolute;left:0;right:0;bottom:0;height:4px;background:var(--gold);
  }

  /* Front – navy */
  .card--front{background:var(--navy)}
  .front-pattern{
    position:absolute;inset:0;
    background:linear-gradient(135deg,var(--navy-soft) 0%,var(--navy) 45%,var(--navy-deep) 100%);
  }
  .brand{
    position:absolute;display:flex;align-items:center;gap:14px;
    font-family:"Montserrat",sans-serif;font-weight:700;
    text-transform:uppercase;letter-spacing:.06em;white-space:nowrap;
  }
  .brand__mark{display:block;flex:none;background:var(--gold)}
  .card--front .brand{left:50%;top:50%;transform:translate(-50%,-50%);color:var(--white);font-size:36px}
  .card--front .brand__mark{width:14px;height:14px}

  /* Back – white */
  .card--back{background:var(--white)}
  .card--back .brand{
    left:40px;top:96px;width:210px;
    color:var(--navy);font-size:24px;line-height:1.15;gap:12px;
  }
  .card--back .brand__mark{width:12px;height:12px;align-self:flex-start;margin-top:7px}
  .brand__name{display:block}
  .brand__name span{display:block}
  .divider{position:absolute;left:268px;top:34px;width:2px;height:190px;background:var(--navy)}
  .details{position:absolute;left:290px;top:34px;width:250px;color:var(--ink)}
  .person{font-family:"Montserrat",sans-serif;font-weight:800;font-size:25px;line-height:1;white-space:nowrap}
  .person__first{color:var(--gold)}
  .person__last{color:var(--navy)}
  .role{font-family:"Montserrat",sans-serif;font-weight:700;font-size:12px;color:var(--ink);margin-top:5px}
  .address{font-size:11px;line-height:1.45;margin-top:14px}
  .contacts{list-style:none;margin-top:12px;font-size:11px;line-height:1.75}
  .contacts li{display:flex;align-items:center;gap:7px;white-space:nowrap}
  .contacts svg{width:11px;height:11px;flex:none}
  .bands{position:absolute;left:0;bottom:0;width:560px;height:110px}
</style>
</head>
<body>

  <section class="card card--front" aria-label="Card front">
    <div class="front-pattern" role="img" aria-label="Subtle repeating brand pattern on navy"></div>
    <div class="brand"><span class="brand__mark"></span>Harbor Crestline</div>
  </section>

  <section class="card card--back" aria-label="Card back">
    <div class="brand"><span class="brand__mark"></span><span class="brand__name"><span>Harbor</span><span>Crestline</span></span></div>
    <div class="divider"></div>
    <div class="details">
      <p class="person"><span class="person__first">Dorian</span> <span class="person__last">Fenwick</span></p>
      <p class="role">CEO/Founder</p>
      <p class="address">2140 Larkmoor Ave<br>Suite 410, Ellsworth, MD 21306</p>
      <ul class="contacts">
        <li>
          <svg viewBox="0 0 24 24" fill="var(--gold)"><path d="M6.6 10.8a15.1 15.1 0 0 0 6.6 6.6l2.2-2.2a1 1 0 0 1 1-.25 11.4 11.4 0 0 0 3.6.57 1 1 0 0 1 1 1V20a1 1 0 0 1-1 1A17 17 0 0 1 3 4a1 1 0 0 1 1-1h3.5a1 1 0 0 1 1 1c0 1.250.2 2.450.57 3.570a1 1 0 0 1-.25 1z"/></svg>
          (833) HarbCre / (833) 427-2731
        </li>
        <li>
          <svg viewBox="0 0 24 24" fill="none" stroke="var(--gold)" stroke-width="2.4"><circle cx="12" cy="12" r="9"/><path d="M3 12h18M12 3c3 3.5 3 14.5 0 18M12 3c-3 3.5-3 14.5 0 18"/></svg>
          www.theharborcrestline.com
        </li>
        <li>
          <svg viewBox="0 0 24 24" fill="none" stroke="var(--gold)" stroke-width="2.4"><rect x="3" y="5" width="18" height="14" rx="1"/><path d="M3 6l9 7 9-7"/></svg>
          dorian@theharborcrestline.com
        </li>
      </ul>
    </div>
    <svg class="bands" viewBox="0 0 560 110" preserveAspectRatio="none" aria-hidden="true">
      <path d="M0 84 L300 84 Q318 84 332 70 L360 46 L560 46 L560 58 L372 58 L348 80 Q334 96 312 96 L0 96 Z" fill="var(--gold)"/>
      <path d="M344 38 L376 14 Q388 6 406 6 L560 6 L560 32 L360 32 Z" fill="var(--navy)"/>
    </svg>
  </section>

</body>
</html>
```